need corporate, modern business card created for Consulting Company

I need a slick business card using elements from my website, as well as, integrating my pixelforge-created logo (see files).

The business card needs to be:
1. Corporate and modern
2. Clean and professional

I've included a PSD with the logo/icon that you can use to create it. Feel free to try a metallic finish on the logo, make it bigger/small, underlay it. Whatever you need to do to make my card stand out.

Try a black background, or white background or gray.

The idea is for my card to be memorable as well as professional and corporate.

Target Market(s)

Corporate business in the US and Canada.

Industry/Entity Type

Business

Contact Information for Business Card

Commerce Advancing Methods
Martin Coles, Senior Partner
office: 1 877 555 0143
mobile: 1 519 555 0172
website: http://www.brightvale.example

Requirements
Must have
• Card-related information
• corporate, yet modern
• clean and professional
• incorporate the icon only
• must have an editable form when complete!
Nice to have
• metallic icon might be cool
• try it with white or black

```html
<!DOCTYPE html>
<html lang="en">
<head>
<meta charset="utf-8">
<title>Brightvale Business Card</title>
<link rel="stylesheet" href="https://fonts.googleapis.com/css2?family=Saira:wght@400;500;600&display=swap">
<style>
  :root {
    --page-bg: #e4e3e0;
    --card-blue: #2f6cb6;
    --card-black: #1c1c1e;
    --arc-grey: #a9a9ad;
    --text-light: #ffffff;
    --brand-blue: #3d7ccc;
  }
  html, body {
    margin: 0;
    width: 1200px;
    height: 900px;
    overflow: hidden;
    background: var(--page-bg);
    font-family: "Saira", sans-serif;
  }
  .canvas {
    position: relative;
    width: 1200px;
    height: 900px;
  }
  .business-card {
    position: absolute;
    left: 75px;
    top: 150px;
    width: 1050px;
    height: 600px;
    overflow: hidden;
    box-shadow: 0 10px 30px rgba(0,0,0,0.18);
  }
  .card-shapes {
    position: absolute;
    inset: 0;
  }
  .contact-side {
    position: absolute;
    left: 70px;
    top: 66px;
    color: var(--text-light);
  }
  .holder-name {
    margin: 0;
    font-size: 36px;
    font-weight: 500;
    letter-spacing: 2px;
    text-transform: uppercase;
    line-height: 1.1;
  }
  .holder-title {
    margin: 4px 0 0;
    font-size: 22px;
    font-weight: 400;
    letter-spacing: 0.5px;
  }
  .office-address {
    margin: 42px 0 0;
    font-size: 22px;
    font-style: normal;
    line-height: 1.3;
    letter-spacing: 0.5px;
  }
  .contact-list {
    list-style: none;
    margin: 34px 0 0;
    padding: 0;
    font-size: 21px;
    letter-spacing: 1.5px;
  }
  .contact-list li {
    display: flex;
    align-items: center;
    height: 40px;
  }
  .contact-list .text-item { font-size: 18px; letter-spacing: 0.5px; }
  .contact-icon {
    width: 21px;
    height: 21px;
    margin-right: 15px;
    flex: none;
  }
  .brand-lockup {
    position: absolute;
    left: 590px;
    top: 275px;
    display: flex;
    align-items: center;
    gap: 18px;
  }
  .brand-square {
    width: 40px;
    height: 40px;
    background: var(--brand-blue);
  }
  .brand-name {
    font-size: 62px;
    font-weight: 600;
    color: var(--brand-blue);
    line-height: 1;
    letter-spacing: 1px;
  }
</style>
</head>
<body>
<main class="canvas">
  <section class="business-card">
    <svg class="card-shapes" width="1050" height="600" viewBox="0 0 1050 600" aria-hidden="true">
      <rect width="1050" height="600" fill="var(--card-blue)"/>
      <circle cx="1150" cy="420" r="720" fill="var(--card-black)"/>
      <circle cx="1150" cy="420" r="695" fill="var(--arc-grey)"/>
      <circle cx="1175" cy="430" r="695" fill="var(--card-black)"/>
    </svg>

    <div class="contact-side">
      <h1 class="holder-name">Martin Coles</h1>
      <p class="holder-title">Senior Partner</p>
      <address class="office-address">120 Harbour Street, Suite 400<br>Halton, ON</address>
      <ul class="contact-list">
        <li>
          <svg class="contact-icon" viewBox="0 0 24 24"><path fill="#fff" d="M6.6 10.8a15 15 0 0 0 6.6 6.6l2.2-2.2c.3-.3.7-.4 1-.2 1.1.4 2.3.6 3.6.6.6 0 1 .4 1 1V20c0 .6-.4 1-1 1A17 17 0 0 1 3 4c0-.6.4-1 1-1h3.5c.6 0 1 .4 1 1 0 1.3.2 2.5.6 3.6.1.3 0 .7-.2 1z"/></svg>
          1 877 555 0143
        </li>
        <li>
          <svg class="contact-icon" viewBox="0 0 24 24"><rect x="6" y="2" width="12" height="20" rx="2" fill="none" stroke="#fff" stroke-width="2"/><circle cx="12" cy="18" r="1.3" fill="#fff"/></svg>
          1 519 555 0172
        </li>
        <li>
          <svg class="contact-icon" viewBox="0 0 24 24"><rect x="3" y="9" width="18" height="12" fill="#fff"/><rect x="7" y="3" width="8" height="7" fill="none" stroke="#fff" stroke-width="2"/></svg>
          1 877 555 0198
        </li>
        <li class="text-item">
          <svg class="contact-icon" viewBox="0 0 24 24"><rect x="2" y="5" width="20" height="14" fill="#fff"/><path d="M2 5l10 8 10-8" fill="none" stroke="var(--card-blue)" stroke-width="1.8"/></svg>
          mcoles@brightvale.example
        </li>
        <li class="text-item">
          <svg class="contact-icon" viewBox="0 0 24 24"><circle cx="12" cy="12" r="9.5" fill="none" stroke="#fff" stroke-width="2"/><path d="M2.5 12h19M12 2.5c3 3 3 16 0 19M12 2.5c-3 3-3 16 0 19" fill="none" stroke="#fff" stroke-width="1.5"/></svg>
          www.brightvale.example
        </li>
      </ul>
    </div>

    <div class="brand-lockup">
      <span class="brand-square"></span>
      <span class="brand-name">brightvale</span>
    </div>
  </section>
</main>
</body>
</html>
```